The Visual Personality of Miss Cobbler Food Trailer

Something that stands out with color and our logo. This is a food trailer that attends several events in the spring and summer. We are known for being one of the best Gumbo producers in mid Michigan. We have been responsible for connecting different communities and cultures together and we are strong supporters of our veterans since this is a veteran owned business. All of our vegetables are fresh and locally purchased. These recipes are originally from New Orleans Louisiana. Our website is Misscobbler.net. This will be used for an 8" x 11" poster. Leave a box or area that states "WHERE WE WILL BE:" so that we can add the location of the event that we are attending.

Target Market(s)

We do cuisine that is recognized in the southern states of the USA. but live in the northern part of the USA. We are providing a menu of different southern recipes so they do not have to go all the way down south for get..

Industry/Entity Type

Food/Restaurant Industry

Font styles to use
Serif
Decorative

Colors
0094D4
00A9DD
6FCCEA
C7EBF8
E9F6FB
59FF00
82FF00
B8FF75
E3FFCB
F4FFEA
FFF300
FFF600
FEFA6F
FFFEC7
FFFEE8
EE7325
F08F49
F5BC92
FAE3D3
FDF4ED
EB3D1F
EC4F4E
F09395
F8D3D4
FCEDEE
A7469A
B969AE
D3A5CF
EDDBEB
F8F0F9

Requirements
Must have
• Our logo, which is "Miss Cobbler", "Homemade Deliciousness". We need an area on the poster where we can manually add the location of the event we will be attending because it changes weekly. location
Nice to have
• Bold colors and logo

```html
<!DOCTYPE html>
<html lang="en">
<head>
<meta charset="utf-8">
<title>Miss Cobbler Food Trailer – Poster</title>
<link rel="stylesheet" href="https://fonts.googleapis.com/css2?family=Italianno&family=Prata&family=Libre+Baskerville:wght@700&family=Lato:wght@400&display=swap">
<style>
  :root {
    --brand-pink: #e4325b;
    --brand-pink-dark: #c9244b;
    --paper: #ffffff;
    --backdrop: #6b6c70;
    --ink: #3a3a3a;
    --stripe: #ececec;
    --pin-red: #e8141c;
  }
  * { box-sizing: border-box; margin: 0; padding: 0; }
  html, body { width: 1200px; height: 1200px; overflow: hidden; }
  body { background: var(--backdrop); position: relative; font-family: "Lato", sans-serif; }

  .poster {
    position: absolute; left: 152px; top: 20px;
    width: 896px; height: 1160px;
    background: var(--paper); overflow: hidden;
  }

  .hero-photo {
    position: absolute; left: 0; top: 0; width: 896px; height: 529px;
    background: linear-gradient(135deg, #8a5a36 0%, #a8784f 35%, #e9e4da 55%, #b88a5d 75%, #9a6a42 100%);
  }
  .hero-shapes { position: absolute; left: 0; top: 0; }

  .brand-badge {
    position: absolute; left: 676px; top: -25px;
    width: 266px; height: 266px; border-radius: 50%;
    background: var(--paper); border: 17px solid var(--brand-pink);
    display: flex; align-items: center; justify-content: center;
  }
  .brand-badge__name {
    font-family: "Prata", serif; font-size: 30px; color: var(--brand-pink);
    margin-right: 40px; margin-top: 20px; text-align: center; line-height: 1.1;
  }

  .dish {
    position: absolute; border: 13px solid var(--paper); border-radius: 30px;
    transform: rotate(45deg); overflow: hidden;
    box-shadow: 0 6px 14px rgba(0,0,0,0.28);
  }
  .dish--shrimp { left: 77px; top: 331px; width: 210px; height: 210px;
    background: linear-gradient(135deg, #e9d3a8, #d9653f 45%, #e8c390 70%, #9c8a5a); }
  .dish--gumbo { left: 331px; top: 294px; width: 230px; height: 230px;
    background: radial-gradient(circle at 50% 50%, #d2553a 0%, #c84a2f 45%, #8fa24a 70%, #e9e2d6 90%); }
  .dish--sandwich { left: 610px; top: 331px; width: 210px; height: 210px;
    background: linear-gradient(135deg, #dcd3c4, #c98a48 40%, #d4463a 65%, #e6dcc2); }

  .tagline-band {
    position: absolute; left: 0; top: 529px; width: 896px; height: 276px;
    background: var(--brand-pink); color: var(--paper); text-align: center;
  }
  .tagline-band__script {
    position: absolute; left: 0; right: 0; top: 55px;
    font-family: "Italianno", cursive; font-size: 96px; line-height: 1;
  }
  .tagline-band__sub {
    position: absolute; left: 0; right: 0;
    font-family: "Prata", serif; font-size: 36px; line-height: 1;
  }
  .tagline-band__sub--one { top: 154px; }
  .tagline-band__sub--two { top: 202px; }
  .tagline-band__rule {
    display: inline-block; width: 42px; height: 2px; background: var(--paper);
    vertical-align: middle; margin: 0 6px;
  }

  .location-map {
    position: absolute; left: 440px; top: 805px; width: 456px; height: 291px;
    background: radial-gradient(ellipse at 75% 70%, #dcdcdc 0%, #efefef 45%, #ffffff 80%);
  }
  .location-pin { position: absolute; left: 730px; top: 760px; }

  .location {
    position: absolute; left: 22px; top: 838px; width: 520px;
  }
  .location__title {
    font-family: "Libre Baskerville", serif; font-weight: 700;
    font-size: 42px; color: var(--brand-pink); line-height: 1; letter-spacing: 0.5px;
    display: inline-block; white-space: nowrap;
    border-bottom: 2px solid var(--brand-pink);
    padding: 0 2px 6px 2px;
  }
  .location__details {
    margin-top: 18px; margin-left: 9px; width: 452px;
    font-size: 18px; line-height: 31px; color: var(--ink);
  }

  .contact-bar {
    position: absolute; left: 0; top: 1096px; width: 896px; height: 64px;
    background: var(--brand-pink);
  }
  .contact-bar__divider { position: absolute; left: 0; top: 0; }
  .contact-bar__phone {
    position: absolute; left: 64px; top: 0; height: 64px;
    display: flex; align-items: center; gap: 10px;
    color: var(--paper); font-size: 22px;
  }
  .contact-bar__web {
    position: absolute; right: 80px; top: 0; height: 64px;
    display: flex; align-items: center; color: var(--paper); font-size: 21px;
  }
</style>
</head>
<body>
  <div class="poster">
    <div class="hero-photo" role="img" aria-label="Photo of fresh green pepper, tomato, onion and a soup container on a wooden board"></div>

    <svg class="hero-shapes" width="896" height="529" viewBox="0 0 896 529">
      <polygon points="0,127 0,529 452,529" fill="#e4325b"/>
      <polygon points="0,157 0,529 418,529" fill="#f6f6f6"/>
      <polygon points="790,230 830,230 896,220 896,529 560,529" fill="#e4325b"/>
      <polygon points="825,235 896,235 896,529 596,529" fill="#f6f6f6"/>
    </svg>

    <div class="brand-badge">
      <span class="brand-badge__name">Miss Cobbler</span>
    </div>

    <div class="dish dish--shrimp" role="img" aria-label="Photo of shrimp and grits topped with diced tomato"></div>
    <div class="dish dish--sandwich" role="img" aria-label="Photo of a po'boy sandwich with chips"></div>
    <div class="dish dish--gumbo" role="img" aria-label="Photo of a bowl of gumbo with vegetables"></div>

    <section class="tagline-band">
      <p class="tagline-band__script">Homemade Deliciousness</p>
      <p class="tagline-band__sub tagline-band__sub--one">Created From Fresh And</p>
      <p class="tagline-band__sub tagline-band__sub--two"><span class="tagline-band__rule"></span>Authentic Ingredients<span class="tagline-band__rule"></span></p>
    </section>

    <div class="location-map" role="img" aria-label="Illustration of a light street map with a winding road"></div>
    <svg class="location-pin" width="112" height="176" viewBox="0 0 112 176" aria-hidden="true">
      <path d="M56 4 C26 4 4 28 4 58 C4 96 40 120 56 172 C72 120 108 96 108 58 C108 28 86 4 56 4 Z" fill="#e8141c" stroke="#ffffff" stroke-width="4"/>
      <circle cx="56" cy="56" r="30" fill="#ffffff"/>
    </svg>

    <section class="location">
      <h2 class="location__title">Where We Will Be</h2>
      <p class="location__details">Lorem ipsum dolor sit amet, consectetuer adipiscing elit, sed diam nonummy nibh euismod tincidunt ut laoreet dolore magna aliquam erat volutpat. Ut wisi enim ad minim veniam, quis nostrud exerci tation ullamcorp</p>
    </section>

    <footer class="contact-bar">
      <svg class="contact-bar__divider" width="896" height="64" viewBox="0 0 896 64">
        <polygon points="389,0 427,0 476,64 437,64" fill="#ffffff"/>
      </svg>
      <div class="contact-bar__phone">
        <svg width="24" height="24" viewBox="0 0 24 24" aria-hidden="true">
          <path d="M6.6 10.8c1.4 2.8 3.8 5.1 6.6 6.6l2.2-2.2c.3-.3.7-.4 1-.2 1.1.4 2.3.6 3.6.6.6 0 1 .4 1 1V20c0 .6-.4 1-1 1C10.6 21 3 13.4 3 4c0-.6.4-1 1-1h3.5c.6 0 1 .4 1 1 0 1.3.2 2.5.6 3.6.1.3 0 .7-.2 1L6.6 10.8z" fill="#ffffff"/>
          <path d="M15 3a6 6 0 0 1 6 6M15 6a3 3 0 0 1 3 3" stroke="#ffffff" stroke-width="1.6" fill="none"/>
        </svg>
        <span>555-014-2287</span>
      </div>
      <div class="contact-bar__web">www.misscobbler.net</div>
    </footer>
  </div>
</body>
</html>
```